SkyvornQ Business Cards and Stationary Design

Need a design for our business cards and stationary. I want to carry on the theme of the logo. I want the business cards to have a design on the back. I would like the business cards and the stationary to carry the same theme, design scheme, and branding

Target Market(s)

Airlines and Maintenance Facilities

Industry/Entity Type

Aviation

Contact Information for Business Card

Name
Position Title
Address: 4827 Trellis Hollow Road, Fort Pierce, Florida, 34951
Office Number
Mobile Number
Email
Website

Font styles to use
Serif
Sans Serif

Colors

Designer to choose colors to be used in the design.

```html
<!DOCTYPE html>
<html lang="en">
<head>
<meta charset="utf-8">
<title>SkyvornQ Business Card</title>
<link rel="stylesheet" href="https://fonts.googleapis.com/css2?family=Open+Sans:wght@400;700&display=swap">
<style>
  :root {
    --bg: #e4e1de;
    --card: #ffffff;
    --navy: #14305f;
    --blue: #1f5fae;
    --sky: #3b8fd6;
    --grey-text: #6b6b6b;
    --rule: #b9bcc2;
    --band: #9a9ea6;
  }
  * { margin: 0; padding: 0; box-sizing: border-box; }
  html, body { width: 1200px; height: 997px; overflow: hidden; }
  body {
    background: var(--bg);
    font-family: "Open Sans", Arial, sans-serif;
    position: relative;
  }
  .card {
    position: absolute;
    width: 640px;
    height: 366px;
    background: var(--card);
    box-shadow: 0 6px 18px rgba(0,0,0,0.12);
    overflow: hidden;
  }
  .card--front { left: 120px; top: 90px; }
  .card--back { left: 440px; top: 540px; }

  /* Front */
  .brand {
    position: absolute;
    display: flex;
    align-items: center;
    gap: 14px;
  }
  .brand__mark {
    width: 42px; height: 42px;
    border-radius: 50%;
    background: var(--blue);
  }
  .brand__name {
    font-weight: 700;
    color: var(--navy);
    letter-spacing: 5px;
    text-transform: uppercase;
  }
  .card--front .brand { left: 60px; top: 78px; }
  .card--front .brand__name { font-size: 28px; }

  .person { position: absolute; right: 60px; top: 62px; text-align: right; }
  .person__name { font-size: 18px; font-weight: 700; color: var(--navy); letter-spacing: 0.5px; }
  .person__title { font-size: 13px; color: var(--grey-text); margin-top: 1px; }
  .person__rule { width: 150px; height: 3px; background: var(--navy); margin: 8px 0 0 auto; }

  .website {
    position: absolute; right: 30px; top: 176px;
    font-size: 13px; color: var(--grey-text); letter-spacing: 0.5px;
  }
  .divider {
    position: absolute; left: 0; right: 0; top: 200px; height: 1px;
    background: var(--rule);
  }
  .band {
    position: absolute; right: 0; top: 197px; width: 270px; height: 7px;
    background: var(--band);
  }
  .band__accent {
    position: absolute; right: 0; top: 197px; width: 120px; height: 12px;
    background: var(--navy);
  }
  .contacts {
    position: absolute; left: 60px; top: 232px;
    list-style: none;
  }
  .contacts li {
    display: flex; align-items: center; gap: 10px;
    font-size: 15px; color: var(--grey-text);
    line-height: 24px;
  }
  .contacts svg { width: 13px; height: 13px; fill: var(--navy); }

  /* Back */
  .card--back .brand {
    left: 0; right: 0; top: 118px; justify-content: center;
  }
  .card--back .brand__mark { width: 56px; height: 56px; }
  .card--back .brand__name { font-size: 38px; letter-spacing: 7px; }
  .address {
    position: absolute; left: 0; right: 0; top: 232px;
    text-align: center; font-size: 17px; color: var(--grey-text); letter-spacing: 0.5px;
  }
</style>
</head>
<body>
  <section class="card card--front">
    <div class="brand">
      <span class="brand__mark"></span>
      <span class="brand__name">SkyvornQ</span>
    </div>
    <div class="person">
      <div class="person__name">DORIAN VALE</div>
      <div class="person__title">President</div>
      <div class="person__rule"></div>
    </div>
    <div class="website">www.skyvornq.com</div>
    <div class="divider"></div>
    <div class="band"></div>
    <div class="band__accent"></div>
    <ul class="contacts">
      <li>
        <svg viewBox="0 0 16 16" aria-hidden="true"><path d="M2 5c0-2 2-3 6-3s6 1 6 3v1h-3V4.5H5V6H2zM4 7h8l2 7H2z"/></svg>
        001 555 0187
      </li>
      <li>
        <svg viewBox="0 0 16 16" aria-hidden="true"><rect x="4" y="1" width="8" height="14" rx="1.5"/></svg>
        001 555 0187
      </li>
      <li>
        <svg viewBox="0 0 16 16" aria-hidden="true"><path d="M1 3h14v10H1z M1 3l7 6 7-6" /></svg>
        info@skyvornq.com
      </li>
    </ul>
  </section>

  <section class="card card--back">
    <div class="brand">
      <span class="brand__mark"></span>
      <span class="brand__name">SkyvornQ</span>
    </div>
    <div class="address">4827 Trellis Hollow Road, Fort Pierce, Florida, 34951</div>
  </section>
</body>
</html>
```